Business card for a new innovative and professional lawn care business

We need a business card design for a new lawn care business in Halifax NS Canada. We offer lawn services in Halifax & Bedford. Our services offered include lawn care, garden services, and property maintenance. We take pride in our work and are experienced at what we do. I would like to see a design that is double sided. On the backside I would like the something simple (maybe my logo preferably on blackround (linked below) with website link, Facebook page or something). The front I want to include contact info:
Morgan Pell
phone 902-555-0148
email - brookvaleyards.ca
facebook - Facebook.com/brookvaleyards
Instagram maybe ? - instagram.com/brookvaleyard
Serving Halifax and Bedford for 5 years?
I don't want it to have too much information as I will be passing them out in aim to visit website, or call !
We do want it to include lawn care, garden services and property maintenance.
Basic, catchy, and modern looking !
Logo attached below !

Target Market(s)

Passing business cards to everyone I meet or interact with.

Industry/Entity Type

Lawn Care

Contact Information for Business Card

Double sided with some basic information, with catchy colours and easy to look at.

Font styles to use
Sans Serif

Requirements
Must have
• Must be double sided and have :
• Name, Phone, Email, FB, Website, and 3 main services offered - lawn care, property maintenance, garden services
Nice to have
• Would be nice to have instagram link if it goes well on there
Should not have
• Don't want too much writing or images that are distracting

```html
<!DOCTYPE html>
<html lang="en">
<head>
<meta charset="utf-8">
<title>Brookvale Yards – Business Card</title>
<link href="https://fonts.googleapis.com/css2?family=Arimo:wght@400;700&family=Michroma&display=swap" rel="stylesheet">
<style>
  :root {
    --stage: #1c1c1c;
    --card-dark: #333333;
    --card-light: #f7f7f7;
    --lime: #7dc242;
    --forest: #1f7a35;
    --ink: #3a3a3a;
    --white: #ffffff;
  }
  * { box-sizing: border-box; margin: 0; padding: 0; }
  html, body {
    width: 1200px; height: 873px; overflow: hidden;
    background: var(--stage);
  }
  .stage {
    width: 1200px; height: 873px;
    display: flex; align-items: center; justify-content: center; gap: 40px;
  }
  .card {
    position: relative;
    width: 520px; height: 297px;
    overflow: hidden;
    box-shadow: 0 10px 30px rgba(0,0,0,.5);
  }

  /* Back side */
  .card--back { background: var(--card-dark); }
  .card--back .wordmark {
    position: absolute; top: 92px; left: 0; right: 0;
    text-align: center;
  }
  .wordmark__name {
    font-family: "Arimo", sans-serif; font-weight: 700;
    font-size: 38px; letter-spacing: 2px; color: var(--lime);
    text-transform: uppercase;
  }
  .wordmark__dot {
    display: inline-block; width: 14px; height: 14px; border-radius: 50%;
    background: var(--lime); margin-right: 12px; vertical-align: 4px;
  }
  .service-band {
    position: absolute; left: 0; right: 0; bottom: 0; height: 46px;
    background: var(--lime);
    display: flex; align-items: center; justify-content: center; gap: 28px;
    font-family: "Arimo", sans-serif; font-weight: 700; font-size: 14px;
    color: var(--card-dark);
  }
  .service-band li { list-style: none; display: flex; align-items: center; }
  .service-band li::before {
    content: ""; width: 9px; height: 9px; border-radius: 50%;
    background: var(--white); margin-right: 8px;
  }

  /* Front side */
  .card--front { background: var(--card-light); }
  .card--front .wordmark {
    position: absolute; top: 50px; left: 60px;
  }
  .card--front .wordmark__name { font-size: 30px; }
  .holder {
    position: absolute; top: 116px; right: 40px; text-align: right;
  }
  .holder__name {
    font-family: "Arimo", sans-serif; font-weight: 700; font-size: 20px;
    color: var(--lime); text-transform: uppercase; letter-spacing: .5px;
  }
  .holder__role {
    font-family: "Arimo", sans-serif; font-size: 14px; color: var(--ink);
    letter-spacing: 1px; margin-top: 3px;
  }
  .contacts {
    position: absolute; left: 36px; top: 160px; list-style: none;
    font-family: "Michroma", sans-serif; font-size: 11.5px; color: var(--ink);
  }
  .contacts li { display: flex; align-items: center; height: 20px; }
  .contacts svg, .contacts .mark {
    width: 13px; height: 13px; margin-right: 12px; flex: none;
  }
  .contacts .mark { background: var(--lime); border-radius: 2px; }
  .web-band {
    position: absolute; left: 0; right: 0; bottom: 0; height: 50px;
    background: var(--lime);
    display: flex; align-items: center; justify-content: center;
    font-family: "Arimo", sans-serif; font-weight: 700; font-size: 16px;
    letter-spacing: 3px; color: var(--white);
  }
  .web-band .tld { color: var(--forest); }
</style>
</head>
<body>
<main class="stage">

  <section class="card card--back" aria-label="Card back">
    <div class="wordmark">
      <span class="wordmark__dot"></span><span class="wordmark__name">Brookvale Yards</span>
    </div>
    <ul class="service-band">
      <li>Lawn Care</li>
      <li>Property Maintenance</li>
      <li>Garden Services</li>
    </ul>
  </section>

  <section class="card card--front" aria-label="Card front">
    <div class="wordmark">
      <span class="wordmark__dot"></span><span class="wordmark__name">Brookvale Yards</span>
    </div>

    <div class="holder">
      <p class="holder__name">Morgan Pell</p>
      <p class="holder__role">Owner / Director</p>
    </div>

    <ul class="contacts">
      <li>
        <svg viewBox="0 0 16 16" aria-hidden="true"><path fill="#7dc242" d="M3 1h3l1.5 4-2 1.3a9 9 0 0 0 4.2 4.2L11 8.5l4 1.5v3a2 2 0 0 1-2 2A12 12 0 0 1 1 3a2 2 0 0 1 2-2z"/></svg>
        902-555-0148
      </li>
      <li>
        <svg viewBox="0 0 16 16" aria-hidden="true"><rect x="1" y="3" width="14" height="10" rx="1.5" fill="#7dc242"/><path d="M1.5 4 8 9l6.5-5" stroke="#fff" stroke-width="1.4" fill="none"/></svg>
        brookvaleyards.ca
      </li>
      <li><span class="mark" aria-hidden="true"></span>/brookvaleyards</li>
      <li><span class="mark" aria-hidden="true"></span>/brookvaleyard</li>
    </ul>

    <div class="web-band">www.brookvaleyards<span class="tld">.ca</span></div>
  </section>

</main>
</body>
</html>
```